BOLD & MINIMALIST DESIGN NEEDED

We want a very bold but minimalistic business card design that is impactful and utilizes both sides of the business card. Our current logo is included for your use.

We want bold fonts and good use of negative space. We don't want the logo to overpower the design.

Target Market(s)

Professionals who are building new commercial buildings.

Industry/Entity Type

Construction

Contact Information for Business Card

Name, Title, email, office phone, cell phone, website

Font styles to use
Serif
Sans Serif

Requirements
Must have
• Bold design!

```html
<!DOCTYPE html>
<html lang="en">
<head>
<meta charset="UTF-8">
<title>Ridgewell Business Card</title>
<link href="https://fonts.googleapis.com/css2?family=Poppins:wght@400;600;700&display=swap" rel="stylesheet">
<style>
  :root {
    --stage: #262626;
    --card-top: #1c1c1d;
    --card-bottom: #232324;
    --green: #7dc242;
    --white: #f2f2f2;
    --soft: #d8d8d8;
  }
  * { margin: 0; padding: 0; box-sizing: border-box; }
  html, body { width: 1200px; height: 576px; overflow: hidden; }
  body {
    background: var(--stage);
    font-family: "Poppins", sans-serif;
    position: relative;
  }
  .card {
    position: absolute;
    top: 139px;
    width: 482px;
    height: 292px;
    border-radius: 9px;
    background: linear-gradient(160deg, var(--card-top), var(--card-bottom));
    box-shadow: 0 3px 8px rgba(0,0,0,0.45);
  }
  .card-front { left: 102px; }
  .card-back { left: 596px; }

  .brand {
    position: absolute;
    display: flex;
    align-items: center;
    gap: 10px;
    color: var(--white);
    font-weight: 700;
    letter-spacing: 1px;
    white-space: nowrap;
  }
  .brand-mark {
    background: var(--green);
    flex: none;
  }
  .card-front .brand {
    left: 50%;
    top: 50%;
    transform: translate(-50%, -50%);
    font-size: 34px;
  }
  .card-front .brand-mark { width: 26px; height: 26px; }
  .card-back .brand {
    right: 30px;
    bottom: 40px;
    font-size: 21px;
    gap: 7px;
  }
  .card-back .brand-mark { width: 16px; height: 16px; }

  .holder { position: absolute; left: 30px; top: 30px; }
  .holder-name {
    color: var(--green);
    font-size: 21px;
    font-weight: 600;
    line-height: 1.2;
  }
  .holder-title {
    color: var(--white);
    font-size: 12px;
    font-weight: 400;
    margin-top: 2px;
  }

  .contacts {
    position: absolute;
    left: 30px;
    top: 213px;
    list-style: none;
  }
  .contacts li {
    display: flex;
    align-items: center;
    gap: 8px;
    color: var(--soft);
    font-size: 12px;
    line-height: 17px;
  }
  .contacts svg { width: 10px; height: 10px; fill: var(--green); flex: none; }
</style>
</head>
<body>
  <section class="card card-front">
    <div class="brand"><span class="brand-mark"></span>RIDGEWELL</div>
  </section>

  <section class="card card-back">
    <div class="holder">
      <div class="holder-name">Tomas Reyes</div>
      <div class="holder-title">Director</div>
    </div>
    <ul class="contacts">
      <li>
        <svg viewBox="0 0 10 10"><path d="M1 3 Q5 0 9 3 L8 4.5 L6.5 3.8 L6.5 3 Q5 2.5 3.5 3 L3.5 3.8 L2 4.5 Z M2.5 5 L7.5 5 L8.5 9 L1.5 9 Z"/></svg>
        005-005-0005
      </li>
      <li>
        <svg viewBox="0 0 10 10"><path d="M0.5 2 L9.5 2 L5 5.5 Z M0.5 3 L5 6.5 L9.5 3 L9.5 8 L0.5 8 Z"/></svg>
        tomas@ridgewell.com
      </li>
      <li>
        <svg viewBox="0 0 10 10"><circle cx="5" cy="5" r="4.5"/><path d="M0.5 5 H9.5 M5 0.5 V9.5" stroke="#1f1f20" stroke-width="0.8"/></svg>
        www.ridgewell.com
      </li>
    </ul>
    <div class="brand"><span class="brand-mark"></span>RIDGEWELL</div>
  </section>
</body>
</html>
```